BRV Early College and Career Program

Starting a new program initiative at Birchmont Valley School where students will have the opportunity to take college courses during their senior year of high school. Preferably add some pictures to reflect the career pathways we are offering (below) Some context to use for this flyer are:

Learn more about the career focused courses in…
• Education
• Computer & Information Science
• Technology & Engineering
• Health

Things to look forward to:
Experience college in high school
Finish college early
Save money on college tuition and fees
Advice on Career pathways

all classes fit into OPAL CREDIT BUNDLE

For more information contact

Gavin Purdy - ZT12 Alliances -WHVC
555.014.2291
Email: gpurdy@whvc-example.edu

Ms. Okafuji- Early College Coordinator
Email: dena.okafuji@birchmont-example.org
Room J215

I uploaded 5 or so photos that I would like to see incorporated in the design of the flier- using real students from our high school will give a more realistic approach- thanks, Added Monday, August 21, 2017

Target Market(s)

High school students who are currently in 10th grade (for recruitment) and only high school juniors and seniors are able to apply.

Industry/Entity Type

School

Colors

Designer to choose colors to be used in the design.

Requirements
Must have
• logos- some pictures reflecting the different career pathways and the contact information provided. Looking to also have this in a format that I can print on card stock paper not just full length page- ADD / USE photos attached to see which one fits the project better.
Nice to have
• suitable for high school students- attractive
Should not have
• Do not include any generic phone numbers.

```html
<!DOCTYPE html>
<html lang="en">
<head>
<meta charset="utf-8">
<title>BRV Early College Program</title>
<link rel="stylesheet" href="https://fonts.googleapis.com/css2?family=Source+Sans+3:wght@400;600;700&family=PT+Sans+Narrow:wght@700&display=swap">
<style>
  :root {
    --navy: #1b3a6b;
    --blue: #4a86c8;
    --sky: #5b93d1;
    --grey: #cfd4da;
    --white: #ffffff;
    --text-grey: #5d6470;
    --soft: #c9d6e8;
  }
  * { margin: 0; padding: 0; box-sizing: border-box; }
  html, body { width: 992px; height: 1200px; overflow: hidden; background: var(--white); }
  .flyer {
    position: relative; width: 992px; height: 1200px; overflow: hidden;
    font-family: "Source Sans 3", sans-serif; background: var(--white);
  }
  .backdrop, .student-photo { position: absolute; left: 0; top: 0; }
  .partners { position: absolute; top: 58px; right: 18px; display: flex; gap: 16px; align-items: center; }
  .partner { display: flex; align-items: center; gap: 8px; font-weight: 600; color: var(--navy); font-size: 17px; line-height: 1.05; }
  .partner-mark { width: 30px; height: 30px; border-radius: 50%; background: var(--navy); flex: none; }
  .partner-college { background: var(--navy); color: var(--white); padding: 10px 12px; width: 228px; }
  .partner-college .partner-mark { background: var(--blue); border-radius: 0; }
  .title {
    position: absolute; left: 420px; width: 572px; top: 216px; text-align: center;
    color: var(--white); font-weight: 600; font-size: 40px; line-height: 1.2;
  }
  .tagline {
    position: absolute; left: 600px; width: 360px; top: 378px; text-align: center;
    font-family: "PT Sans Narrow", sans-serif; font-weight: 700; color: var(--navy); font-size: 23px; line-height: 1.17;
  }
  .perks { position: absolute; left: 36px; top: 527px; }
  .perks h2 { font-size: 20px; font-weight: 700; color: var(--navy); margin-bottom: 4px; }
  .perks ul { list-style: none; }
  .perks li { font-size: 20px; color: var(--text-grey); line-height: 29px; display: flex; align-items: center; gap: 8px; }
  .perks li::before {
    content: "›"; width: 14px; height: 14px; border-radius: 50%; background: var(--blue); color: var(--white);
    font-size: 13px; line-height: 12px; text-align: center; font-weight: 700; flex: none;
  }
  .pathway { position: absolute; width: 240px; text-align: center; color: var(--white); font-weight: 600; font-size: 19px; line-height: 1.3; text-transform: uppercase; }
  .contact-banner {
    position: absolute; left: 548px; top: 904px; width: 444px; height: 50px;
    color: var(--white); font-size: 19px; display: flex; align-items: center; padding-left: 54px;
  }
  .contact { position: absolute; top: 1030px; color: var(--soft); font-size: 17px; line-height: 26px; }
  .contact h3 { color: var(--white); font-size: 21px; font-weight: 600; line-height: 28px; }
  .contact .email { color: var(--white); font-size: 16px; letter-spacing: -0.2px; display: flex; align-items: center; gap: 7px; }
  .contact .email::before { content: ""; width: 13px; height: 9px; background: var(--blue); flex: none; }
</style>
</head>
<body>
<main class="flyer">
  <svg class="backdrop" width="992" height="1200" viewBox="0 0 992 1200" aria-hidden="true">
    <polygon points="0,860 992,516 992,1159 0,1159" fill="var(--navy)"/>
    <polygon points="0,832 992,488 992,516 0,860" fill="var(--blue)"/>
    <rect x="0" y="1168" width="992" height="32" fill="var(--blue)"/>
    <polygon points="320,0 350,0 676,504 646,504" fill="var(--grey)"/>
    <polygon points="292,0 320,0 646,504 618,504" fill="var(--blue)"/>
    <polygon points="440,196 992,196 992,345 536,345" fill="var(--navy)"/>
    <polygon points="432,188 992,188 992,193 436,193" fill="var(--blue)"/>
    <polygon points="536,350 992,350 992,356 540,356" fill="var(--blue)"/>

    <g class="icon-education">
      <circle cx="140" cy="802" r="86" fill="var(--grey)"/>
      <circle cx="140" cy="802" r="78" fill="var(--sky)"/>
      <polygon points="140,764 204,790 140,816 76,790" fill="var(--white)"/>
      <path d="M104 802 v22 q36 18 72 0 v-22 l-36 14 z" fill="var(--white)"/>
      <rect x="186" y="792" width="4" height="46" fill="var(--white)"/>
    </g>
    <g class="icon-computing">
      <circle cx="386" cy="748" r="86" fill="var(--grey)"/>
      <circle cx="386" cy="748" r="78" fill="var(--sky)"/>
      <rect x="372" y="740" width="56" height="38" rx="3" fill="none" stroke="var(--white)" stroke-width="5"/>
      <rect x="362" y="780" width="76" height="6" fill="var(--white)"/>
      <circle cx="374" cy="722" r="14" fill="none" stroke="var(--white)" stroke-width="8" stroke-dasharray="5 4"/>
      <circle cx="350" cy="750" r="9" fill="none" stroke="var(--white)" stroke-width="6" stroke-dasharray="4 3"/>
    </g>
    <g class="icon-technology">
      <circle cx="615" cy="664" r="86" fill="var(--grey)"/>
      <circle cx="615" cy="664" r="78" fill="var(--sky)"/>
      <circle cx="615" cy="664" r="30" fill="none" stroke="var(--white)" stroke-width="14" stroke-dasharray="9 6"/>
      <circle cx="615" cy="664" r="22" fill="none" stroke="var(--white)" stroke-width="6"/>
      <ellipse cx="615" cy="664" rx="40" ry="13" fill="none" stroke="var(--white)" stroke-width="3" transform="rotate(35 615 664)"/>
    </g>
    <g class="icon-health">
      <circle cx="858" cy="578" r="86" fill="var(--grey)"/>
      <circle cx="858" cy="578" r="78" fill="var(--sky)"/>
      <rect x="854" y="532" width="8" height="92" rx="3" fill="var(--white)"/>
      <path d="M858 548 q-38 -16 -56 4 q26 -4 56 10 q30 -14 56 -10 q-18 -20 -56 -4z" fill="var(--white)"/>
      <path d="M842 570 q32 10 0 24 q-30 10 2 22" fill="none" stroke="var(--white)" stroke-width="5"/>
      <path d="M874 570 q-32 10 0 24 q30 10 -2 22" fill="none" stroke="var(--white)" stroke-width="5"/>
    </g>
    <polygon points="572,904 992,904 992,954 548,954" fill="var(--blue)"/>
  </svg>

  <svg class="student-photo" width="992" height="504" viewBox="0 0 992 504" role="img" aria-label="Photo of two smiling students standing beside a camera tripod">
    <defs>
      <linearGradient id="photoTone" x1="0" y1="0" x2="1" y2="1">
        <stop offset="0" stop-color="#8a8683"/>
        <stop offset="0.5" stop-color="#4a4546"/>
        <stop offset="1" stop-color="#1f1d22"/>
      </linearGradient>
    </defs>
    <polygon points="0,0 292,0 618,504 0,504" fill="url(#photoTone)"/>
  </svg>

  <div class="partners">
    <div class="partner"><span class="partner-mark"></span><span>Birchmont<br>Public Schools</span></div>
    <div class="partner partner-college"><span class="partner-mark"></span><span>Westhaven Valley<br>Community College</span></div>
  </div>

  <h1 class="title">BRV Early College<br>Program</h1>
  <p class="tagline">Earn credit for both High School and College and Learn more about the career focused courses in</p>

  <section class="perks">
    <h2>THINGS TO LOOK FORWARD TO:</h2>
    <ul>
      <li>Experience college in high school</li>
      <li>Finish college early</li>
      <li>Save money on college tuition and fees</li>
      <li>Get advice on your future career</li>
    </ul>
  </section>

  <p class="pathway" style="left:20px; top:905px;">Education</p>
  <p class="pathway" style="left:266px; top:847px;">Computer &amp;<br>Information Science</p>
  <p class="pathway" style="left:495px; top:763px;">Technology &amp;<br>Engineering</p>
  <p class="pathway" style="left:738px; top:677px;">Health</p>

  <div class="contact-banner">FOR MORE INFORMATION CONTACT</div>

  <div class="contact" style="left:52px;">
    <h3>Gavin Purdy</h3>
    <p>ZT12 Alliances</p>
    <p>WHVC</p>
    <p class="email">gpurdy@whvc-example.edu</p>
  </div>
  <div class="contact" style="left:330px;">
    <h3>Ms. Okafuji</h3>
    <p>Early College Coordinator</p>
    <p>Room J215</p>
    <p class="email">dena.okafuji@birchmont-example.org</p>
  </div>
  <div class="contact" style="left:667px;">
    <h3>Ms. Halvorsen</h3>
    <p>Work-Based Learning Coordinator</p>
    <p>Room J215</p>
    <p class="email">mira.halvorsen@birchmont-example.org</p>
  </div>
</main>
</body>
</html>
```